Sunset Harbor Living Web Page

We need a web page design that has two intro pages - first being a 'home page', then a link to the second page that has the 'content tabs' and a 'call to action' (see below).

The business helps people that wish to retire to S.E.Asia (Thailand, Malaysia, Indonesia,The Philippines etc) - to enjoy the lifestyle and the remaining years of their lives. What attracts S.E.Asia to many people is the lower cost, the atmoshpere and beauty of the tropics and the vibrancy of the various countries.

People that are wishing to make the most of their retirement and are adventurous at a great bargain compared to the cost of their own countries will be interested.

We help them achieve this - visa, financials (tax, gov't payments etc), introduce them to the right people for property, clubs, retirement facilities, insurance and so forth.

Therefore we are providing an extremely wide ranging service and this site will provide broad but general information only - with a call to action to come and see us for more specific information and how we can help them specifically.

This site will be predominantly for travel and lifestyle, it will be linked with another financial services (financial planning) site later down the track.

The colour scheme is dark green and blue - as per the attached logo design. Photos and background just think lifestyle and S.E.Asia - beaches/mountains/water/recreational activities for retirees.

Target market is mostly those coming up to retirement to those that are already retired. But we also expect to have some interest with younger people that would like to find out more and plan for the future. So a broad age group but I would say mostly 40-70 yrs old.

On the first (Home) page we would like our company name 'Sunset Harbor Living', our logo (which will be on all pages) and a statement such as: “Imagine a retirement where your dreams are brought to life, and you have never felt more alive. Let us show you how”. Then a link to the second page.

We would like an uncluttered site. On the second (contents) page the tabs would be:

- Visa
- Property
- Financials
- Travel
- Insurance & Healthcare
- Medical Tourism
- Cost of living
- Weekly Blogs and articles
- Sunset Harbor Living story

We would also like a call to action on the second page - asking them to leave their contact details if they wish to learn more or sign up to our weekly newsletter/blog.

We are open to suggestions and your imaginations.

Thank you
Malcolm

Font styles to use
Serif
Script

Colors
0255a3
3377b5
00a990
9bcb3c
abd036
33b8a4
85abd2
cadf82
86cfc6

Requirements
Must have
• I have been asked by the web designer to receive a 'Web Font' so that we can 'get off of Zentrofy'. Hope that makes sense.

```html
<!DOCTYPE html>
<html lang="en">
<head>
<meta charset="utf-8">
<title>Sunset Harbor Living</title>
<link href="https://fonts.googleapis.com/css2?family=Maven+Pro:wght@400;500;700&family=Open+Sans:ital,wght@0,400;0,600;0,700;1,600&display=swap" rel="stylesheet">
<style>
:root{
  --blue:#0255a3;
  --blue-mid:#3377b5;
  --blue-soft:#85abd2;
  --teal:#00a990;
  --teal-soft:#33b8a4;
  --green:#9bcb3c;
  --green-bright:#abd036;
  --green-pale:#cadf82;
  --ink:#222;
  --muted:#666;
  --line:#e3e3e3;
  --head:'Maven Pro',sans-serif;
  --body:'Open Sans',sans-serif;
}
*{box-sizing:border-box;margin:0;padding:0}
html,body{width:1200px;height:3056px;overflow:hidden}
body{position:relative;background:#fff;font-family:var(--body);color:var(--ink)}
a{color:inherit;text-decoration:none}
.abs{position:absolute}

/* header */
.brand{left:161px;top:34px;display:flex;align-items:center;gap:10px}
.brand-dot{width:44px;height:44px;border-radius:50%;background:var(--green)}
.brand-name{font-family:var(--head);font-weight:700;font-size:25px;color:var(--blue);line-height:1}
.call{left:664px;top:33px;display:flex;align-items:center;gap:10px;font-family:var(--head);font-size:24px;color:var(--green);font-weight:500}
.call b{color:var(--blue);font-weight:700}
.login{left:972px;top:30px;width:71px;height:33px;background:var(--green);color:#fff;font-size:12px;font-weight:700;display:flex;align-items:center;justify-content:center}
.subnav{left:533px;top:92px;width:667px;height:38px;background:var(--green);clip-path:polygon(16px 0,100% 0,100% 100%,0 100%);display:flex;align-items:center;padding-left:50px;gap:50px;color:#fff;font-size:12.5px;font-weight:600}
.mainnav{left:0;top:130px;width:1200px;height:45px;background:var(--blue);display:flex;padding-left:161px;color:#fff;font-size:12.5px;font-weight:600}
.mainnav a{display:flex;align-items:center;padding:0 28px}
.mainnav a.active{background:var(--green);padding:0 31px}

/* hero */
.hero{left:0;top:175px;width:1200px;height:489px;background:linear-gradient(100deg,#c9a56d 0%,#a98a5b 30%,#6f6a5c 55%,#4a5559 100%)}
.hero-title{left:768px;top:312px;font-family:var(--head);font-size:41px;font-weight:500;color:#fff}
.hero-text{left:686px;top:374px;width:352px;text-align:right;color:#f1f1f1;font-size:12.5px;line-height:19px}
.btn{display:inline-flex;align-items:center;gap:7px;color:#fff;font-size:11px;font-weight:700;height:33px;padding:0 14px;text-transform:uppercase}
.btn-green{background:var(--green)}
.btn-blue{background:var(--blue)}
.btn-teal{background:var(--teal)}
.hero-btn{left:931px;top:460px}
.arrow{width:34px;height:34px;border:2px solid rgba(255,255,255,.8);border-radius:50%;top:388px}

/* features */
.features{left:161px;top:682px;width:880px;display:flex}
.feature{width:310px;display:flex;gap:14px}
.feature:first-child{width:300px}
.f-icon{width:57px;height:57px;border-radius:50%;flex:none;margin-top:18px;display:flex;align-items:center;justify-content:center}
.feature h3{font-family:var(--head);font-size:18px;font-weight:500;margin-bottom:8px}
.feature p{font-size:11px;color:var(--muted);line-height:18px;width:200px}

/* about */
.about{left:161px;top:808px;width:894px;height:316px;border:1px solid var(--line);display:flex}
.about-media{width:538px;height:100%;background:linear-gradient(120deg,#e7b866 0%,#c98c4c 45%,#7e6a58 100%);position:relative}
.play{left:240px;top:128px;width:60px;height:60px;border-radius:50%;background:rgba(30,30,30,.7);border:3px solid #fff;display:flex;align-items:center;justify-content:center}
.about-copy{padding:36px 0 0 50px;width:350px}
.about-copy h2{font-family:var(--head);font-weight:500;font-size:26px;margin-bottom:20px}
.about-copy p{font-size:11px;color:var(--muted);line-height:19.5px;margin-bottom:22px}
.about-copy .btn{height:41px;padding:0 20px}

/* section heading */
.sec-head{left:0;width:1200px;display:flex;justify-content:center;align-items:center;gap:12px;font-family:var(--head);font-size:26px;font-weight:500;color:#333}
.sec-head i{width:30px;height:30px;border-radius:50%;background:#5a5a5a;display:block}
.sec-sub{left:0;top:1212px;width:1200px;text-align:center;font-size:12px;color:#444}

/* destinations */
.destinations{left:155px;top:1263px;width:878px;display:grid;grid-template-columns:repeat(3,283px);gap:12px 14px}
.dest{height:285px;position:relative;border-bottom:4px solid var(--teal-soft);display:flex;align-items:center;justify-content:center}
.dest span{border:2px solid #fff;color:#fff;font-family:var(--head);font-weight:500;font-size:17px;width:180px;height:34px;display:flex;align-items:center;justify-content:center;background:rgba(0,0,0,.15)}
.d1{background:linear-gradient(160deg,#4f6a3a,#2f6f6c 70%,#2a8a8a)}
.d2{background:linear-gradient(180deg,#c87a4d,#8e5a49 50%,#5a3a32)}
.d3{background:linear-gradient(180deg,#d08c4a,#8a6142 55%,#3d3a33)}
.d4{background:linear-gradient(180deg,#6f9a58,#4e7c3a 50%,#3b6a2e)}
.d5{background:linear-gradient(180deg,#d48a6a,#4d7b87 55%,#2a8d8e)}
.d6{background:linear-gradient(180deg,#7a9a60,#5c8a49 60%,#4b6b3c)}

/* lifestyle band */
.lifestyle{left:0;top:1884px;width:1200px;height:381px}
.life-copy{left:161px;top:1966px;width:530px;color:#fff}
.life-copy h2{font-family:var(--head);font-weight:700;font-size:24px;display:flex;align-items:center;gap:10px;margin-bottom:14px}
.life-copy h2 i{width:30px;height:30px;border-radius:50%;background:#fff;display:block}
.life-copy h4{font-size:14.5px;font-weight:700;margin-bottom:14px}
.life-copy p{font-size:11px;line-height:18px;color:#e8eef3}

/* blog */
.blog{left:161px;top:2324px;width:880px;display:flex;gap:36px}
.post{width:270px}
.post-media{height:163px;position:relative}
.post-date{left:0;top:0;width:48px;height:56px;color:#fff;font-size:10px;padding:6px 0 0 8px;line-height:1.2}
.post-date b{display:block;font-family:var(--head);font-size:22px}
.post h3{font-family:var(--head);font-size:18px;font-weight:700;margin:24px 0 10px}
.post p{font-size:11px;line-height:18px;color:#555;margin-bottom:16px}

/* newsletter */
.newsletter{left:0;top:2693px;width:1200px;height:61px;background:var(--green);display:flex;align-items:center;padding-left:118px}
.newsletter .env{width:34px;height:22px;background:var(--green-pale);transform:rotate(-15deg);margin-right:10px;border-radius:2px}
.newsletter h3{font-family:var(--head);font-weight:500;font-size:21px;color:#fff;width:334px}
.field{width:224px;height:34px;background:#fff;font-size:11px;font-style:italic;color:#555;display:flex;align-items:center;padding-left:8px;margin-right:6px}
.newsletter .subscribe{width:94px;height:34px;background:var(--blue);color:#fff;font-size:12px;font-weight:700;display:flex;align-items:center;justify-content:center;margin-left:2px}

/* footer */
.footer{left:0;top:2754px;width:1200px;height:302px;background:var(--blue);color:#fff}
.foot-col{position:absolute;top:54px;font-size:11px}
.foot-col h4{font-size:12.5px;font-weight:700;margin-bottom:18px;text-transform:uppercase}
.foot-col li{list-style:none;line-height:20.5px;display:flex;gap:8px}
.foot-col li::before{content:"›";}
.contact li::before{content:none}
.contact li{line-height:19px;margin-bottom:2px}
.contact svg{flex:none;margin-top:4px}
.socials{display:flex;gap:8px;margin-top:10px}
.socials i{width:23px;height:23px;border-radius:50%;border:1px solid #fff;display:block}
.socials i:first-child{background:var(--green);border-color:var(--green)}
.gallery{display:grid;grid-template-columns:repeat(3,83px);gap:7px}
.gallery div{height:64px}
.copyright{position:absolute;left:0;top:264px;width:1200px;text-align:center;font-size:10px;color:#dbe6f2}
</style>
</head>
<body>

<header>
  <a class="abs brand" href="#"><span class="brand-dot"></span><span class="brand-name">Sunset Harbor Living</span></a>
  <div class="abs call">
    <svg width="28" height="28" viewBox="0 0 28 28"><circle cx="14" cy="14" r="12.5" fill="none" stroke="#9bcb3c" stroke-width="2"/><path d="M10 8c1 0 2 2 2 3s-1 1.5-1 2 2.5 3.5 3.5 3.5 1-1 2-1 3 1 3 2-1.5 2.5-3 2.5C12 20 8 15 8 11c0-1.5 1-3 2-3z" fill="#9bcb3c"/></svg>
    <span>Call Us: <b>(555) 214-3390</b></span>
  </div>
  <a class="abs login" href="#">LOG IN</a>
  <nav class="abs subnav"><a href="#">Weekly Blogs and articles</a><a href="#">Sunset Harbor Living story</a><a href="#">Contact us</a></nav>
  <nav class="abs mainnav">
    <a class="active" href="#">Home</a><a href="#">Visa</a><a href="#">Property</a><a href="#">Financials</a><a href="#">Travel</a><a href="#">Insurance &amp; Healthcare</a><a href="#">Medical Tourism</a><a href="#">Cost of living</a>
  </nav>
</header>

<section>
  <div class="abs hero" role="img" aria-label="Photo of a woman sitting on the bow of a boat at sunset on calm water with mountains"></div>
  <h1 class="abs hero-title">Sunset Harbor Living</h1>
  <p class="abs hero-text">Sed ut perspiciatis unde omnis iste natus error sit voluptatem accusantium doloremque <b><i>laudantium, totam rem</i></b> aperiam eaque ipsa quae ab illo inventore veritatis</p>
  <a class="abs btn btn-green hero-btn" href="#">Read more <svg width="12" height="12" viewBox="0 0 12 12"><circle cx="6" cy="6" r="5.5" fill="#fff"/><path d="M5 3.5 7.5 6 5 8.5" stroke="#9bcb3c" stroke-width="1.6" fill="none"/></svg></a>
  <svg class="abs arrow" style="left:30px" viewBox="0 0 34 34"><path d="M19 11 13 17l6 6" stroke="#fff" stroke-width="2" fill="none"/></svg>
  <svg class="abs arrow" style="left:1128px" viewBox="0 0 34 34"><path d="M15 11l6 6-6 6" stroke="#fff" stroke-width="2" fill="none"/></svg>
</section>

<section class="abs features">
  <div class="feature">
    <div class="f-icon" style="background:var(--green)"><svg width="24" height="24" viewBox="0 0 24 24"><circle cx="10" cy="10" r="6" stroke="#fff" stroke-width="2.5" fill="none"/><path d="M14.5 14.5 20 20" stroke="#fff" stroke-width="3"/></svg></div>
    <div><h3>Find</h3><p>Sed ut perspiciatis unde omnis iste natus error sit voluptatem accusantium doloremque laudantium, totam.</p></div>
  </div>
  <div class="feature">
    <div class="f-icon" style="background:var(--teal)"><svg width="24" height="24" viewBox="0 0 24 24"><path d="M4 12l5 5L20 6" stroke="#fff" stroke-width="3" fill="none"/></svg></div>
    <div><h3>Choose</h3><p>Sed ut perspiciatis unde omnis iste natus error sit voluptatem accusantium doloremque laudantium, totam.</p></div>
  </div>
  <div class="feature">
    <div class="f-icon" style="background:var(--blue)"><svg width="24" height="24" viewBox="0 0 24 24"><circle cx="12" cy="12" r="9" stroke="#fff" stroke-width="2" fill="none"/><ellipse cx="12" cy="12" rx="4" ry="9" stroke="#fff" stroke-width="1.6" fill="none"/><path d="M3 12h18" stroke="#fff" stroke-width="1.6"/></svg></div>
    <div><h3>Network</h3><p>Sed ut perspiciatis unde omnis iste natus error sit voluptatem accusantium doloremque laudantium, totam.</p></div>
  </div>
</section>

<section class="abs about">
  <div class="about-media" role="img" aria-label="Photo of a smiling couple by the water at sunset looking at a phone">
    <div class="abs play"><svg width="20" height="22" viewBox="0 0 20 22"><path d="M3 1l16 10L3 21z" fill="#fff"/></svg></div>
  </div>
  <div class="about-copy">
    <h2>About Us</h2>
    <p>Sed ut perspiciatis unde omnis iste natus error sit voluptatem accusantium doloremque laudantium, totam rem aperiam, eaque ipsa quae ab illo inventore veritatis et quasi architecto beatae vitae dicta sunt explicabo. Nemo enim ipsam voluptatem quia voluptas sit aspernatur aut odit aut fugit, sed quia consequuntur magni dolores eos qui ratione voluptatem sequi nesciunt.</p>
    <a class="btn btn-green" href="#">View more <svg width="12" height="12" viewBox="0 0 12 12"><circle cx="6" cy="6" r="5.5" fill="#fff"/><path d="M5 3.5 7.5 6 5 8.5" stroke="#9bcb3c" stroke-width="1.6" fill="none"/></svg></a>
  </div>
</section>

<section>
  <h2 class="abs sec-head" style="top:1166px"><i></i>Explore What Makes you Happy</h2>
  <p class="abs sec-sub">What attracts S.E.Asia to many people is the lower cost,</p>
  <div class="abs destinations">
    <a class="dest d1" href="#" role="img" aria-label="Photo of a long-tail boat among limestone cliffs in Thailand"><span>Thailand</span></a>
    <a class="dest d2" href="#" role="img" aria-label="Photo of a wooden jetty at sunset in Malaysia"><span>Malaysia</span></a>
    <a class="dest d3" href="#" role="img" aria-label="Photo of a temple on a lake at sunset in Indonesia"><span>Indonesia</span></a>
    <a class="dest d4" href="#" role="img" aria-label="Photo of green rice terraces in the Philippines"><span>The Philippines</span></a>
    <a class="dest d5" href="#" role="img" aria-label="Photo of a small boat on a calm island bay at dusk"><span>Island</span></a>
    <a class="dest d6" href="#" role="img" aria-label="Photo of a traveller photographing rice terraces"><span>MORE</span></a>
  </div>
</section>

<section>
  <svg class="abs lifestyle" viewBox="0 0 1200 381" role="img" aria-label="Photo of a surfer riding a turquoise wave">
    <defs><linearGradient id="sea" x1="0" y1="0" x2="1" y2="1"><stop offset="0" stop-color="#3b5060"/><stop offset=".5" stop-color="#2f6a78"/><stop offset="1" stop-color="#1d8c96"/></linearGradient></defs>
    <path d="M0 0 Q 520 80 1200 0 L1200 330 Q 640 250 0 381 Z" fill="url(#sea)"/>
  </svg>
  <div class="abs life-copy">
    <h2><i></i>Enjoy The Lifestyles</h2>
    <h4>Lorem ipsum dolor sit loameutconsectetur adipiscing.</h4>
    <p>Lorem ipsum dolor sit amet, consectetur adipiscing elit, sed do eiusmod tempor incididunt ut labore et dolore magna aliqua. Ut enim ad minim veniam, quis nostrud exercitation ullamco laboris nisi ut aliquip ex ea commodo consequat. Duis aute irure dolor in reprehenderit in voluptate velit esse cillum dolore eu fugiat nulla pariatur.</p>
  </div>
</section>

<section>
  <h2 class="abs sec-head" style="top:2258px"><i></i>Latest Blog News</h2>
  <div class="abs blog">
    <article class="post">
      <div class="post-media" role="img" aria-label="Photo of a family walking on a white sand beach" style="background:linear-gradient(180deg,#8fc7e6,#cfe6ef 55%,#efe6d6)"><div class="abs post-date" style="background:var(--blue)">March<b>20</b></div></div>
      <h3>Lorem ipsum dolor sit loame</h3>
      <p>Lorem ipsum dolor sit amet, consectetur adipiscing elit, sed do eiusmod tempor incididunt ut labore et dolore magna aliqua. Ut enim ad minim veniam, quis nostrud exercitation ullamco laboris nisi.</p>
      <a class="btn btn-blue" href="#">Read more <svg width="12" height="12" viewBox="0 0 12 12"><circle cx="6" cy="6" r="5.5" fill="#fff"/><path d="M5 3.5 7.5 6 5 8.5" stroke="#0255a3" stroke-width="1.6" fill="none"/></svg></a>
    </article>
    <article class="post">
      <div class="post-media" role="img" aria-label="Photo of misty green hills and tea fields" style="background:linear-gradient(180deg,#9aa89a,#5f8a4a 50%,#3f6a2e)"><div class="abs post-date" style="background:var(--green)">March<b>20</b></div></div>
      <h3>Lorem ipsum dolor sit loame</h3>
      <p>Lorem ipsum dolor sit amet, consectetur adipiscing elit, sed do eiusmod tempor incididunt ut labore et dolore magna aliqua. Ut enim ad minim veniam, quis nostrud exercitation ullamco laboris nisi.</p>
      <a class="btn btn-green" href="#">Read more <svg width="12" height="12" viewBox="0 0 12 12"><circle cx="6" cy="6" r="5.5" fill="#fff"/><path d="M5 3.5 7.5 6 5 8.5" stroke="#9bcb3c" stroke-width="1.6" fill="none"/></svg></a>
    </article>
    <article class="post">
      <div class="post-media" role="img" aria-label="Photo of a person relaxing on a float in clear tropical water" style="background:linear-gradient(160deg,#2aa3b5,#47c0c4 50%,#7fd6d0)"><div class="abs post-date" style="background:var(--teal)">March<b>20</b></div></div>
      <h3>Lorem ipsum dolor sit loame</h3>
      <p>Lorem ipsum dolor sit amet, consectetur adipiscing elit, sed do eiusmod tempor incididunt ut labore et dolore magna aliqua. Ut enim ad minim veniam, quis nostrud exercitation ullamco laboris nisi.</p>
      <a class="btn btn-teal" href="#">Read more <svg width="12" height="12" viewBox="0 0 12 12"><circle cx="6" cy="6" r="5.5" fill="#fff"/><path d="M5 3.5 7.5 6 5 8.5" stroke="#00a990" stroke-width="1.6" fill="none"/></svg></a>
    </article>
  </div>
</section>

<section class="abs newsletter">
  <span class="env"></span>
  <h3>Sign up to our weekly newsletter</h3>
  <div class="field">Name:</div>
  <div class="field">Email Address:</div>
  <a class="subscribe" href="#">Subscribe</a>
</section>

<footer class="abs footer">
  <div class="foot-col" style="left:161px">
    <h4>Links</h4>
    <ul><li>Home</li><li>Visa</li><li>Property</li><li>Financials</li><li>Travel</li><li>Insurance &amp; Healthcare</li><li>Life Style</li></ul>
  </div>
  <div class="foot-col" style="left:346px;top:88px">
    <ul><li>Medical Tourism</li><li>Cost of living</li><li>Weekly Blogs and articles</li><li>Sunset Harbor Living story</li><li>Contact us</li></ul>
  </div>
  <div class="foot-col contact" style="left:536px;width:170px">
    <h4>Contact Us</h4>
    <ul>
      <li><svg width="9" height="12" viewBox="0 0 9 12"><path d="M4.5 0A4.5 4.5 0 0 0 0 4.5C0 8 4.5 12 4.5 12S9 8 9 4.5A4.5 4.5 0 0 0 4.5 0z" fill="#fff"/></svg><span>Postal address: PO Box 218, Palm Cove harbour road, suite 12 lorem ipsum</span></li>
      <li><svg width="10" height="10" viewBox="0 0 10 10"><path d="M2 0c.7 0 1.5 1.4 1.5 2S3 3 3 3.3 4.7 5.7 5.5 5.7 6.3 5 7 5s2 .7 2 1.4S8 8.5 7 8.5C4 8.5 1 5 1 2 1 1 1.3 0 2 0z" fill="#fff"/></svg><span>Phone: 555 610 4471</span></li>
      <li><svg width="10" height="8" viewBox="0 0 10 8"><rect width="10" height="8" fill="#fff"/><path d="M0 0l5 4 5-4" stroke="#0255a3" fill="none"/></svg><span>hello@sunsetharborliving.com</span></li>
    </ul>
    <div class="socials"><i></i><i></i><i></i><i></i><i></i></div>
  </div>
  <div class="foot-col" style="left:774px">
    <h4>Snapfolio</h4>
    <div class="gallery">
      <div role="img" aria-label="Beach photo" style="background:linear-gradient(#b7d9ee,#e9dcc5)"></div>
      <div role="img" aria-label="Seaside holiday photo" style="background:linear-gradient(#6fb8d8,#2f8db8)"></div>
      <div role="img" aria-label="Couple on the beach photo" style="background:linear-gradient(#9fd0ea,#d9c6a8)"></div>
      <div role="img" aria-label="Sunset beach photo" style="background:linear-gradient(#d9b98a,#9f8b76)"></div>
      <div role="img" aria-label="Ocean swim photo" style="background:linear-gradient(#4aa6d4,#1e6ea8)"></div>
      <div role="img" aria-label="Beach picnic photo" style="background:linear-gradient(#a9d3e8,#e3d2b2)"></div>
    </div>
  </div>
  <p class="copyright">© 2015 All copyrights reserved.Sunset Harbor Living Privacy Policy And Terms And Conditions</p>
</footer>

</body>
</html>
```